IT’S NOT A CLEANING, IT’S YOUR LIFE! TOP TEN REASONS WHY THIS IS NOT JUST A “CLEANING”

We made a list for our patients to let them know why our hygiene appointments are different than other cleanings. Since this is a lot of information, we would like it easily readable within 4-5 feet but we do not want the post to be HUGE. Please see below:

IT’S NOT A CLEANING, IT’S YOUR LIFE!
TOP TEN REASONS WHY THIS IS NOT JUST A “CLEANING”

10. We make you look better. Healthy teeth and gums are more attractive. Recent studies
show that the smile is the first thing people notice and that people with better looking teeth
are more confident and successful.

9. We can relieve your headaches. During your hygiene visit we evaluate for serious bite
issues, many of which lead to muscle soreness, headaches, and migraines.

8. We check for oral cancer. Oral cancer kills 1 person per hour 24 hours a day. The death rate for oral cancer is higher than cancers we routinely hear about such as cervical, thyroid and skin cancer.

7. We make you smell better. During your hygiene visit we eliminate many of the germs that live under your gum tissue and cause bad breath.

6. We save you money. By utilizing the latest dental technology (digital x-rays, mouth
cameras, and magnification glasses) we can help with early detection of tooth and gum
problems and save you the cost of gum surgery, root canals, and implants.

5. We clean in places you cannot. We clean under the gum line and between teeth where
most of the germs hide and cause dental disease. 40% of the bacteria in your mouth lives in
between your teeth.

4. We prevent pain. We identify tooth decay that can lead to nerve involvement and pain,
root canal, and tooth loss.

3. We save your teeth. Most tooth loss is from periodontal/gum disease. At each visit we
evaluate the health of your gums and bone with our periodontal screening. Periodontal
disease, like high blood pressure, is symptomless until it is in advanced stages.

2. We protect your loved ones. Studies have proven that the bacteria that cause dental
disease can be transmitted from person to person. Think about that the next time you kiss
someone!

1. We prolong life. Researchers have linked the inflammation and infection found in the
mouth to heart attacks, strokes, and Alzheimer’s. By reducing infection in your mouth we can
greatly improve your overall health!

```html
<!DOCTYPE html>
<html lang="en">
<head>
<meta charset="utf-8">
<title>It's Not a Cleaning, It's Your Life!</title>
<link rel="stylesheet" href="https://fonts.googleapis.com/css2?family=Jost:wght@300;400&display=swap">
<style>
  :root {
    --page: #ffffff;
    --navy-deep: #06101f;
    --navy: #0b1f3a;
    --teal: #2f8ea3;
    --teal-soft: rgba(70, 160, 180, 0.28);
    --box-line: rgba(160, 210, 225, 0.18);
    --ink: #e4eef3;
    --title: #f3f7fa;
  }
  * { margin: 0; padding: 0; box-sizing: border-box; }
  html, body { width: 776px; height: 1200px; overflow: hidden; background: var(--page); }
  .poster {
    position: absolute; left: 14px; top: 14px; width: 747px; height: 1174px; overflow: hidden;
    background:
      radial-gradient(ellipse 70% 55% at 0% 48%, rgba(60, 160, 180, 0.85), transparent 70%),
      linear-gradient(90deg, var(--teal) 0%, var(--navy) 55%, var(--navy-deep) 100%);
    font-family: 'Jost', sans-serif; color: var(--ink);
  }
  .header-bands { position: absolute; left: 0; top: 0; width: 747px; height: 210px; }
  .title {
    position: absolute; left: 22px; top: 68px;
    font-size: 30px; font-weight: 400; letter-spacing: 0.5px; color: var(--title);
    transform: rotate(-1.2deg); transform-origin: left center; white-space: nowrap;
  }
  .subtitle {
    position: absolute; left: 24px; top: 126px;
    font-size: 23.5px; font-weight: 300; letter-spacing: 0.6px; color: var(--title);
    transform: rotate(-1.2deg); transform-origin: left center; white-space: nowrap;
  }
  .reasons {
    position: absolute; left: 30px; top: 206px; width: 698px; height: 950px;
    list-style: none; display: flex; flex-direction: column; justify-content: space-between;
  }
  .reason {
    background: linear-gradient(90deg, var(--teal-soft), rgba(20, 50, 80, 0.35));
    border-top: 1px solid var(--box-line);
    padding: 7px 10px 9px;
    font-size: 16.2px; font-weight: 300; line-height: 20.4px;
  }
</style>
</head>
<body>
<main class="poster">
  <svg class="header-bands" viewBox="0 0 747 210" aria-hidden="true">
    <polygon points="0,0 747,0 747,150 0,196" fill="#07121f" opacity="0.92"/>
    <polygon points="0,104 747,86 747,104 0,122" fill="#1e6f85" opacity="0.55"/>
    <polygon points="0,122 747,104 747,150 0,176" fill="#081627" opacity="0.95"/>
    <polygon points="0,176 747,150 747,160 0,196" fill="#2a7f93" opacity="0.35"/>
  </svg>
  <h1 class="title">IT’S NOT A CLEANING, IT’S YOUR LIFE!</h1>
  <h2 class="subtitle">TOP TEN REASONS WHY THIS IS NOT JUST A “CLEANING”</h2>

  <ol class="reasons">
    <li class="reason">10. We make you look better. Healthy teeth and gums are more attractive.<br>Recent studies show that the smile is the first thing people notice and that people with better looking teeth are more confident and successful.</li>
    <li class="reason">9. We can relieve your headaches. During your hygiene visit we evaluate for serious bite issues, many of which lead to muscle soreness, headaches, and migraines.</li>
    <li class="reason">8. We check for oral cancer. Oral cancer kills 1 person per hour 24 hours a day.<br>The death rate for oral cancer is higher than cancers we routinely hear about such as cervical, thyroid and skin cancer.</li>
    <li class="reason">7. We make you smell better. During your hygiene visit we eliminate many of the germs that live under your gum tissue and cause bad breath.</li>
    <li class="reason">6. We save you money. By utilizing the latest dental technology (digital x-rays, mouth cameras, and magnification glasses) we can help with early detection of tooth and gum problems and save you the cost of gum surgery, root canals, and implants.</li>
    <li class="reason">5. We clean in places you cannot. We clean under the gum line and between teeth where most of the germs hide and cause dental disease. 40% of the bacteria in your mouth lives in between your teeth.</li>
    <li class="reason">4. We prevent pain. We identify tooth decay that can lead to nerve involvement and pain, root canal, and tooth loss.</li>
    <li class="reason">3. We save your teeth. Most tooth loss is from periodontal/gum disease. At each visit we evaluate the health of your gums and bone with our periodontal screening. Periodontal disease, like high blood pressure, is symptomless until it is in advanced stages.</li>
    <li class="reason">2. We protect your loved ones. Studies have proven that the bacteria that cause dental disease can be transmitted from person to person. Think about that the next time you kiss someone</li>
    <li class="reason">1. We prolong life. Researchers have linked the inflammation and infection found in the mouth to heart attacks, strokes, and Alzheimer’s. By reducing infection in your mouth we can greatly improve your overall health!</li>
  </ol>
</main>
</body>
</html>
```